Design eines Hausetiketts für traditionelles Weingut
Zielgruppe
Wir das Familienweingut Brandauer in Gimbsheim/Rheinhessen sind ein traditionelles Weingut das seine Reben selbst kultiviert und die Weine auch selbst ausbaut. Wir haben jeden Schritt in der Weinherstellung selbst in der Hand und vermarkten den Wein dann an unsere Privatkunden. Unsere Kundenstruktur sieht folgendermaßen aus: Wir haben 100% Privatkunden die unseren Wein konsumieren. Da jetzt die nächste Generation in den Weinbaubetrieb einsteigt und auch Ideen hat möchten wir ein Hausetikett einführen. Im Moment haben wir noch sehr viele unterschiedliche Etiketten und kein Hausetikett. Da die Verlagsetiketten immer seltener zu unseren Vorstellungen passen, möchten wir hier auf diesem Wege ein Hausetikett anfertigen lassen. Generell möchten wir unseren Außenauftritt komplett modernisieren. Sie können sich über die Vielfalt in unserem Betrieb unter www.weingut-brandauer-beispiel.de einen Überblick verschaffen. Langfristig gesehen wollen wir aber unsere Weinkarte verkleinern.
Aufgabenstellung
Wir haben uns vor ca. 1,5 Jahren hier auf dieser Website bereits ein Logo designen lassen. Es wäre schön wenn man das Logo bei den Entwürfen für die Etiketten berücksichtigen würde. Das wäre aber KEIN MUSS. Auch wäre es gut wenn man das ,,Wein' bei unserem Namen weglassen könnte.
Das Etikett sollte aus Vorder-und Rückenetikett bestehen und edel wirken. Vorne sollte die Rebsorte und die Geschmacksangabe stehen. Der Rest sollte auf das Rückenetikett.
Das Vorderetikett sollte ein richtiger Eyecatcher sein und im Supermarkt z.B. aus vielen anderen herausstechen. Das wäre ganz wichtig.
Man kann bei den Farben unterscheiden in 3 Konzepte.
Literwein als einsteiger Wein
Dann die Gutsweine und zum Schluss die Lagenweine. Alles Farblich oder im design etwas abgesetzt.

```html
<!DOCTYPE html>
<html lang="de">
<head>
<meta charset="utf-8">
<title>Brandauer – Hausetikett Dornfelder Rotwein</title>
<link rel="stylesheet" href="https://fonts.googleapis.com/css2?family=Cinzel:wght@400&family=Pinyon+Script&family=Oswald:wght@400&family=Arimo:wght@400&display=swap">
<style>
  :root {
    --page: #ffffff;
    --gold-center: #a8875a;
    --gold-edge: #6b4a1c;
    --band-line: #b4b2ae;
    --dark-corner: #4d3f2c;
    --dark-mid: #1e1913;
    --oval: #0f0d0a;
    --name-light: #4a3a22;
    --name-dark: #c9a86f;
    --berry: #c1272d;
    --white: #ffffff;
  }
  * { margin: 0; padding: 0; box-sizing: border-box; }
  html, body {
    width: 948px; height: 1200px; overflow: hidden;
    background: var(--page);
  }
  .sheet { position: relative; width: 948px; height: 1200px; }

  .label {
    position: absolute; left: 0; width: 948px; overflow: hidden;
  }
  .label--gold {
    top: 9px; height: 579px;
    background: radial-gradient(ellipse 62% 80% at 50% 8%, var(--gold-center) 0%, #95733f 55%, var(--gold-edge) 100%);
  }
  .label--dark {
    top: 601px; height: 578px;
    background: radial-gradient(ellipse 70% 75% at 50% 52%, var(--dark-mid) 40%, var(--dark-corner) 100%);
  }

  .label__oval {
    position: absolute; left: 121px; top: 47px; width: 722px; height: 458px;
    border-radius: 50%;
    background: var(--oval);
  }

  .label__band-line {
    position: absolute; left: 0; top: 498px; width: 100%; height: 7px;
    background: var(--band-line);
  }

  .label__mark {
    position: absolute; left: 50%; top: 150px;
    width: 34px; height: 34px; margin-left: -17px;
    border-radius: 50%; background: var(--berry);
  }

  .label__name {
    position: absolute; left: 0; width: 100%; top: 232px;
    text-align: center;
    font-family: "Cinzel", "Trajan Pro", serif;
    font-weight: 400; font-size: 90px; line-height: 1;
    letter-spacing: -1px;
  }
  .label--gold .label__name { color: var(--name-light); }
  .label--dark .label__name { color: var(--name-dark); }

  .label__variety {
    position: absolute; left: 0; width: 100%; top: 394px;
    text-align: center; color: var(--white);
    font-family: "Pinyon Script", cursive;
    font-size: 29px; line-height: 1;
  }
  .label__vintage {
    position: absolute; left: 0; width: 100%; top: 443px;
    text-align: center; color: var(--white);
    font-family: "Oswald", sans-serif;
    font-size: 27px; line-height: 1; letter-spacing: 0.5px;
  }

  .label__info {
    position: absolute; top: 518px; line-height: 1; color: var(--white);
  }
  .label__info--alcohol, .label__info--volume {
    font-family: "Oswald", sans-serif; font-size: 23px;
  }
  .label__info--alcohol { left: 24px; }
  .label__info--volume { right: 13px; }
  .label__info--number {
    left: 0; width: 100%; text-align: center;
    font-family: "Arimo", Arial, sans-serif; font-size: 17px; letter-spacing: 0.6px;
    top: 526px;
  }
</style>
</head>
<body>
<div class="sheet">

  <section class="label label--gold" aria-label="Etikett Variante Gold">
    <span class="label__mark" aria-hidden="true"></span>
    <h1 class="label__name">BRANDAUER</h1>
    <p class="label__variety">Dornfelder Rotwein</p>
    <p class="label__vintage">2018</p>
    <div class="label__band-line"></div>
    <p class="label__info label__info--alcohol">12,5 %</p>
    <p class="label__info label__info--number">A.P.Nr. 4 281 197 064 19</p>
    <p class="label__info label__info--volume">0.75L</p>
  </section>

  <section class="label label--dark" aria-label="Etikett Variante Dunkel">
    <div class="label__oval"></div>
    <span class="label__mark" aria-hidden="true"></span>
    <h2 class="label__name">BRANDAUER</h2>
    <p class="label__variety">Dornfelder Rotwein</p>
    <p class="label__vintage">2018</p>
    <p class="label__info label__info--alcohol">12,5 %</p>
    <p class="label__info label__info--number">A.P.Nr. 4 281 197 064 19</p>
    <p class="label__info label__info--volume">0.75L</p>
  </section>

</div>
</body>
</html>
```